Graphic design on webpages considering optimisation

Hi,

I would like to make the pages of my website look better. The looks must tie with the landing page, which I will not change.

Ping me an email with any questions. I have been on Pixel Harbour for the brimtower.com page and am very pleased with its looks.

Industry/Entity Type

Graphic Design

```html
<!DOCTYPE html>
<html lang="fr">
<head>
<meta charset="utf-8">
<title>BRIMTOWER – Valeurs Ajoutées</title>
<link href="https://fonts.googleapis.com/css2?family=Roboto:wght@400;500;700&family=Orbitron:wght@700&display=swap" rel="stylesheet">
<style>
:root{
  --page:#f8f8f8;
  --white:#ffffff;
  --blue-top:#2e8dcc;
  --blue-bottom:#17659d;
  --blue-text:#2a7bbf;
  --ink:#1b1b1b;
  --muted:#6a6a6a;
  --line:#dcdcdc;
  --footer:#3a3a3a;
  --card:#f2f2f2;
  --tick:#c9c9c9;
}
*{box-sizing:border-box;margin:0;padding:0}
html,body{width:1200px;height:2284px;overflow:hidden}
body{background:var(--page);font-family:"Roboto",Arial,sans-serif;color:var(--ink);position:relative}
.header-glow{position:absolute;left:73px;top:0;width:1070px;height:92px;background:radial-gradient(ellipse at 50% 0,#fff 60%,rgba(255,255,255,0) 100%)}
.brand{position:absolute;left:79px;top:10px;display:flex;align-items:center;gap:10px}
.brand-square{width:24px;height:24px;background:#8a8a8a}
.brand-name{font-family:"Roboto",Arial,sans-serif;font-weight:700;font-size:32px;letter-spacing:3px;color:#8a8a8a}
.phone{position:absolute;left:860px;top:10px;display:flex;align-items:center;gap:14px;font-size:19px;color:var(--blue-text);letter-spacing:.5px}
.phone svg{width:26px;height:26px}
.nav{position:absolute;left:73px;top:91px;width:1070px;height:46px;display:flex;background:linear-gradient(#fff,#f1f1f1 60%,#d9d9d9);border-bottom:1px solid #cfcfcf}
.nav a{flex:1;display:flex;align-items:center;justify-content:center;font-size:14px;color:#222;text-decoration:none;border-right:1px solid #e2e2e2;padding-top:8px}
.nav a:last-child{border-right:none}
.col-left{position:absolute;left:73px;top:160px;width:239px}
.services{height:270px;background:linear-gradient(var(--blue-top),var(--blue-bottom));border-radius:4px;padding:22px 18px}
.services li{list-style:none;color:#fff;font-size:15px;height:37.5px;display:flex;align-items:center;gap:10px}
.bar{height:49px;background:linear-gradient(var(--blue-top),var(--blue-bottom));color:#fff;font-size:15px;display:flex;align-items:center;padding-left:17px}
.left-bar1{margin-top:22px}
.video{margin-top:21px;width:239px;background:var(--card)}
.video + .video{margin-top:24px}
.video-art{height:156px;background:radial-gradient(ellipse at 50% 55%,#b9dcf5 0,#8cc4ea 28%,#f2f2f2 46%)}
.player{height:26px;background:#111;display:flex;align-items:center;padding:0 8px;gap:6px;color:#bbb;font-size:8px}
.player .track{flex:1;height:3px;background:#444;position:relative}
.player .track::before{content:"";position:absolute;left:0;top:-3px;width:8px;height:8px;border-radius:50%;background:#fff}
.player .time b{color:#e33;font-weight:400}
.doc-bar{margin-top:24px}
.col-main{position:absolute;left:334px;top:160px;width:578px}
.title{height:53px;background:linear-gradient(var(--blue-top),var(--blue-bottom));color:#fff;font-size:18px;font-weight:500;display:flex;align-items:center;padding-left:14px}
.intro{margin-top:22px;font-size:13.4px;line-height:25px;color:var(--ink)}
.intro + .intro{margin-top:20px}
.section-head{font-size:17px;font-weight:700;margin:20px 0 18px}
.benefit{position:relative;padding-left:0;font-size:13.4px;line-height:25px;color:var(--muted);margin-bottom:28px;text-indent:34px}
.benefit svg{position:absolute;left:0;top:2px;width:22px;height:22px}
.gap-big{margin-bottom:58px}
.col-right{position:absolute;left:929px;top:160px;width:219px}
.info-title{color:var(--blue-text);font-size:19px;margin:12px 0 0 37px}
.btn{display:flex;margin-left:37px;width:177px;height:46px;border:1px solid #c8c8c8;border-radius:4px;background:linear-gradient(#fdfdfd,#e4e4e4);align-items:center;justify-content:center;font-size:15.5px;font-weight:700;color:#222}
.btn-first{margin-top:19px}
.btn + .btn{margin-top:15px}
.partners-title{color:var(--blue-text);font-size:19px;margin:24px 0 0 37px}
.partner-badge{margin:20px 0 0 40px;width:160px;height:46px;display:flex;align-items:center;gap:10px}
.partner-badge .sq{width:44px;height:44px;background:#2c4257}
.partner-badge .ln{flex:1;height:18px;background:#2c4257;opacity:.85}
.right-bar{margin-top:13px}
.client{height:236px;background:var(--card);box-shadow:0 2px 3px rgba(0,0,0,.08);padding:16px 18px 0;margin-top:17px}
.client + .client{margin-top:31px}
.client-shot{width:91px;height:84px;margin:0 auto 20px;background:linear-gradient(135deg,#8a6a55,#d7c7b5 45%,#3b2d26)}
.client p{font-size:13px;line-height:25px;color:#333}
.footer{position:absolute;left:0;top:2219px;width:1200px;height:65px;background:var(--footer);color:#eee;font-size:13.5px;display:flex;align-items:center;justify-content:center}
.footer .tag{position:absolute;right:20px;font-size:13px}
</style>
</head>
<body>
<div class="header-glow"></div>
<div class="brand"><span class="brand-square"></span><span class="brand-name">BRIMTOWER</span></div>
<div class="phone">
  <svg viewBox="0 0 26 26"><rect width="26" height="26" rx="3" fill="#2a6fb5"/><path d="M8 6c1 0 2 2 2.5 3.2.3.8-1 1.5-.8 2.2.6 1.7 2 3.2 3.8 4 .7.2 1.3-1.1 2.1-.8 1.2.5 3.3 1.6 3.3 2.6 0 1.3-1.7 2.6-3 2.4C10 18.8 7 15.5 6 9.4 5.8 8 6.7 6 8 6z" fill="#fff"/></svg>
  <span>+33(0)100 482 615</span>
</div>
<nav class="nav">
  <a>Accueil</a><a>Produits</a><a>Valeurs Ajoutées</a><a>Clients</a><a>Service</a><a>Société</a><a>Contact</a>
</nav>

<aside class="col-left">
  <ul class="services">
    <li>→ Nos Services</li><li>→ Conseil</li><li>→ Support</li><li>→ Development</li><li>→ Formation</li><li>→ Decouverte</li>
  </ul>
  <div class="bar left-bar1">Avantages LedgerSphere</div>
  <div class="video"><div class="video-art" role="img" aria-label="Icône nuage avec engrenages"></div><div class="player">▶<div class="track"></div><span class="time">00:00 / <b>00:00</b></span>◀ ● ▭ ▭</div></div>
  <div class="video"><div class="video-art" role="img" aria-label="Icône nuage avec camion de livraison"></div><div class="player">▶<div class="track"></div><span class="time">00:00 / <b>00:00</b></span>◀ ● ▭ ▭</div></div>
  <div class="video"><div class="video-art" role="img" aria-label="Icône nuage avec poignée de main"></div><div class="player">▶<div class="track"></div><span class="time">00:00 / <b>00:00</b></span>◀ ● ▭ ▭</div></div>
  <div class="bar doc-bar">Documentation</div>
  <div class="video"><div class="video-art" role="img" aria-label="Icône de nuage"></div><div class="player">▶<div class="track"></div><span class="time">00:00 / <b>00:00</b></span>◀ ● ▭ ▭</div></div>
</aside>

<main class="col-main">
  <h1 class="title">Valeurs Ajoutées</h1>
  <p class="intro">La très grande majorité d'entre vous est aujourd'hui déjà équipée en progiciel de gestion, alors on peut se demander légitimement : pourquoi changer ?</p>
  <p class="intro">Parce que la suite logicielle LedgerSphere apporte de réels bénéfices, que l'on va détailler ci-dessous… et illustrer de manière personnalisée à votre cas, si vous nous laissez quelques petites informations dans le formulaire suivant : remplir le formulaire</p>
  <h2 class="section-head">Les bénéfices communs à tous les produits LedgerSphere :</h2>
  <p class="benefit gap-big"><svg viewBox="0 0 22 22"><circle cx="11" cy="11" r="10" fill="var(--tick)"/><path d="M6 11l3.5 3.5L16 8" stroke="#fff" stroke-width="2.4" fill="none"/></svg>Les logiciels LedgerSphere sont accessibles via internet en ce qu'on appelle le mode SaaS ou autrement dit dans le Cloud. A moins que vous n'en soyez pas équipés (ce qui devient extrêmement rare) ou que votre Fournisseur d'Accès Internet ne parvient pas à vous fournir un débit raisonnable, vous pourrez profiter de :</p>
  <p class="benefit"><svg viewBox="0 0 22 22"><circle cx="11" cy="11" r="10" fill="var(--tick)"/><path d="M6 11l3.5 3.5L16 8" stroke="#fff" stroke-width="2.4" fill="none"/></svg>Un tarif hyper concurrentiel pour l'utilisation d'un progiciel de gestion (que ce soit l'ERP, le e-commerce, le CRM, LedgerSphere GlobalOne) : en effet, dans le tarif qui vous est proposé, c'est LedgerSphere qui s'occupe de toute la partie machine, administration, sauvegarde, réparation, interventions quelconques sur le système d'exploitation ou l'application (hormis d'éventuels développements spécifiques que vous souhaiteriez), équipements tels que salle machine, climatisation, personnel technique, licences, mises à jour, maintenance (support technique en version anglaise en standard, nous consulter pour un support technique en version française)…d'où des économies substantielles.</p>
  <p class="benefit"><svg viewBox="0 0 22 22"><circle cx="11" cy="11" r="10" fill="var(--tick)"/><path d="M6 11l3.5 3.5L16 8" stroke="#fff" stroke-width="2.4" fill="none"/></svg>Une réactivité hors du commun grâce aux accès internet, de n'importe quel support électronique, PC, portables, tablettes, smartphones,…, de n'importe où (zone couverte par internet ou les réseaux mobiles), à n'importe quel moment.</p>
  <p class="benefit"><svg viewBox="0 0 22 22"><circle cx="11" cy="11" r="10" fill="var(--tick)"/><path d="M6 11l3.5 3.5L16 8" stroke="#fff" stroke-width="2.4" fill="none"/></svg>Des économies conséquentes grâce à l'optimisation du fonctionnement opérationnel : quel que soit le module choisi, par exemple, juste la finance-comptabilité, des processus automatisés apportent rapidité de traitement, taux d'erreurs moindre, réduction de délais de facturation et de paiement, d'où des impacts financiers positifs ou autre exemple : grâce à la gestion des stocks multi-sites, multicanaux, quel que soit le produit acheté par l'un de vos canaux de distribution (points de vente physiques, vente en ligne, vente indirecte via des distributeurs,…), le stock est mis à jour en temps réel, les simulations basées sur l'historique des ventes, éventuellement corrigées de votre vision de gestionnaire expérimenté, évitent ruptures de stocks tout en les maintenant au niveau optimum.</p>
  <p class="benefit"><svg viewBox="0 0 22 22"><circle cx="11" cy="11" r="10" fill="var(--tick)"/><path d="M6 11l3.5 3.5L16 8" stroke="#fff" stroke-width="2.4" fill="none"/></svg>Des économies conséquentes grâce à l'optimisation du fonctionnement opérationnel : quel que soit le module choisi, par exemple, juste la finance-comptabilité, des processus automatisés apportent rapidité de traitement, taux d'erreurs moindre, réduction de délais de facturation et de paiement, d'où des impacts financiers positifs ou autre exemple : grâce à la gestion des stocks multi-sites, multicanaux, quel que soit le produit acheté par l'un de vos canaux de distribution (points de vente physiques, vente en ligne, vente indirecte via des distributeurs,…), le stock est mis à jour en temps réel, les simulations basées sur l'historique des ventes, éventuellement corrigées de votre vision de gestionnaire expérimenté, évitent ruptures de stocks tout en les maintenant au niveau optimum.</p>
  <p class="benefit"><svg viewBox="0 0 22 22"><circle cx="11" cy="11" r="10" fill="var(--tick)"/><path d="M6 11l3.5 3.5L16 8" stroke="#fff" stroke-width="2.4" fill="none"/></svg>Des économies conséquentes grâce à l'optimisation du fonctionnement opérationnel : quel que soit le module choisi, par exemple, juste la finance-comptabilité, des processus automatisés apportent rapidité de traitement, taux d'erreurs moindre, réduction de délais de facturation et de paiement, d'où des impacts financiers positifs ou autre exemple : grâce à la gestion des stocks multi-sites, multicanaux, quel que soit le produit acheté par l'un de vos canaux de distribution (points de vente physiques, vente en ligne, vente indirecte via des distributeurs,…), le stock est mis à jour en temps réel, les simulations basées sur l'historique des ventes, éventuellement corrigées de votre vision de gestionnaire expérimenté, évitent ruptures de stocks tout en les maintenant au niveau optimum.</p>
  <h2 class="section-head">Les bénéfices spécifiques à:</h2>
  <p class="benefit"><svg viewBox="0 0 22 22"><circle cx="11" cy="11" r="10" fill="var(--tick)"/><path d="M6 11l3.5 3.5L16 8" stroke="#fff" stroke-width="2.4" fill="none"/></svg>Des économies conséquentes grâce à l'optimisation du fonctionnement opérationnel : quel que soit le module choisi, par exemple, juste la finance-comptabilité, des processus automatisés apportent rapidité de traitement, taux d'erreurs moindre, réduction de délais de facturation et de paiement, d'où des impacts financiers positifs ou autre exemple : grâce à la gestion des stocks multi-sites, multicanaux, quel que soit le produit acheté par l'un de vos canaux de distribution (points de vente physiques, vente en ligne, vente indirecte via des distributeurs,…), le stock est mis à jour en temps réel, les simulations basées sur l'historique des ventes, éventuellement corrigées de votre vision de gestionnaire expérimenté, évitent ruptures de stocks tout en les maintenant au niveau optimum.</p>
  <p class="benefit"><svg viewBox="0 0 22 22"><circle cx="11" cy="11" r="10" fill="var(--tick)"/><path d="M6 11l3.5 3.5L16 8" stroke="#fff" stroke-width="2.4" fill="none"/></svg>Des économies conséquentes grâce à l'optimisation du fonctionnement opérationnel : quel que soit le module choisi, par exemple, juste la finance-comptabilité, des processus automatisés apportent rapidité de traitement, taux d'erreurs moindre, réduction de délais de facturation et de paiement,</p>
</main>

<aside class="col-right">
  <h3 class="info-title">Une info ?</h3>
  <a class="btn btn-first">Contactez Nous</a>
  <a class="btn">Demand de Devis</a>
  <h3 class="partners-title">Nos Partenariats</h3>
  <div class="partner-badge" role="img" aria-label="Badge partenaire"><span class="sq"></span><span class="ln"></span></div>
  <div class="bar right-bar">Bénéfices client</div>
  <div class="client"><div class="client-shot" role="img" aria-label="Capture du site client"></div><p>Passé de 85 M$ à 130 M$ (meme effectif),<br>Temps traitement à livraison (amélioré de 25%),</p></div>
  <div class="client"><div class="client-shot" role="img" aria-label="Capture du site client"></div><p>Passé de 85 M$ à 130 M$ (meme effectif),<br>Temps traitement à livraison (amélioré de 25%),</p></div>
  <div class="client"><div class="client-shot" role="img" aria-label="Capture du site client"></div><p>Passé de 85 M$ à 130 M$ (meme effectif),<br>Temps traitement à livraison (amélioré de 25%),</p></div>
  <div class="client"><div class="client-shot" role="img" aria-label="Capture du site client"></div><p>Passé de 85 M$ à 130 M$ (meme effectif),<br>Temps traitement à livraison (amélioré de 25%),</p></div>
  <div class="client"><div class="client-shot" role="img" aria-label="Capture du site client"></div><p>Passé de 85 M$ à 130 M$ (meme effectif),<br>Temps traitement à livraison (amélioré de 25%),</p></div>
  <div class="client"><div class="client-shot" role="img" aria-label="Capture du site client"></div><p>Passé de 85 M$ à 130 M$ (meme effectif),<br>Temps traitement à livraison (amélioré de 25%),</p></div>
</aside>

<footer class="footer">Copyright © 2014 brimtower.com. All rights reserved.<span class="tag">c3</span></footer>
</body>
</html>
```